Harbor Loom Floors Letterhead

Letterhead used for business reasons. It must be editable and easy to use.

Address is 2715 W. Pelican Lane Englewood FL 34187 - 941.382.6519

```html
<!DOCTYPE html>
<html lang="en">
<head>
<meta charset="utf-8">
<title>Harbor Loom Floors Letterhead</title>
<link rel="stylesheet" href="https://fonts.googleapis.com/css2?family=Montserrat:wght@400;500;700&family=Great+Vibes&display=swap">
<style>
  :root {
    --backdrop: #e9e9ea;
    --paper: #ffffff;
    --ink: #111111;
    --band: #000000;
    --accent: #e08a20;
    --muted: #3a3a3a;
  }
  * { margin: 0; padding: 0; box-sizing: border-box; }
  html, body {
    width: 1200px; height: 874px; overflow: hidden;
    background: var(--backdrop);
    font-family: "Montserrat", Arial, sans-serif;
    color: var(--ink);
  }
  .letterhead {
    position: absolute; left: 300px; top: 13px;
    width: 600px; height: 848px;
    background: var(--paper);
    box-shadow: 0 2px 10px rgba(0,0,0,0.12);
    overflow: hidden;
  }
  .header-band {
    position: absolute; left: 0; top: 0;
    width: 600px; height: 120px;
    background: var(--band);
    border-bottom: 4px solid var(--accent);
  }
  .brand-name {
    position: absolute; left: 30px; top: 40px;
    font-weight: 500; font-size: 22px; line-height: 1.15;
    letter-spacing: 0.06em; color: var(--accent);
  }
  .contact {
    position: absolute; right: 30px; top: 40px;
    font-style: normal;
    font-size: 8px; line-height: 1.6; color: #d9d9d9;
    padding-left: 10px;
    border-left: 1px solid var(--accent);
  }
  .contact .phone { display: flex; align-items: center; gap: 4px; }
  .contact svg { width: 8px; height: 8px; }
  .letter-body { position: absolute; left: 48px; top: 160px; width: 504px; }
  .date { font-size: 9.5px; margin-bottom: 18px; }
  .recipient { font-size: 9.5px; line-height: 1.3; margin-bottom: 18px; }
  .company-address { font-size: 9.5px; line-height: 1.3; margin-bottom: 26px; }
  .salutation { font-size: 11.5px; font-weight: 700; margin-bottom: 18px; }
  .paragraph { font-size: 8.6px; line-height: 1.45; margin-bottom: 12px; margin-left: 28px; }
  .closing { font-size: 9.5px; margin: 30px 0 16px 56px; }
  .signature {
    font-family: "Great Vibes", cursive;
    font-size: 36px; margin-left: 92px; line-height: 1.1;
  }
</style>
</head>
<body>
  <main class="letterhead">
    <header class="header-band">
      <div class="brand-name">Harbor Loom<br>Floors</div>
      <address class="contact">
        <div>2715 W. Pelican Lane</div>
        <div>Englewood FL 34187</div>
        <div class="phone">
          <svg viewBox="0 0 10 10" aria-hidden="true"><circle cx="5" cy="5" r="5" fill="var(--accent)"/><path d="M3.2,2.6 L4.3,3.7 L3.8,4.4 C4.2,5.2 4.8,5.8 5.6,6.2 L6.3,5.7 L7.4,6.8 L6.7,7.5 C4.8,7.3 2.7,5.2 2.5,3.3 Z" fill="#fff"/></svg>
          <span>941.382.6519</span>
        </div>
      </address>
    </header>

    <section class="letter-body">
      <p class="date">January-03-2020</p>
      <p class="recipient">Mr. Alan Price<br>President</p>
      <p class="company-address">Brightline Corporation<br>123 Street Name, Suite# 10<br>City, State, 120023</p>
      <p class="salutation">Dear Mr. Alan</p>
      <p class="paragraph">Lorem ipsum dolor sit amet, consectetur adipiscing elit, sed do eiusmod tempor incididunt ut labore et dolore magna aliqua. Ut enim ad minim veniam, quis nostrud exercitation ullamco laboris nisi ut aliquip ex ea commodo consequat. Duis aute irure dolor in reprehenderit in voluptate velit esse cillum dolore eu fugiat nulla pariatur.</p>
      <p class="paragraph">Lorem ipsum dolor sit amet, consectetur adipiscing elit, sed do eiusmod tempor incididunt ut labore et dolore magna aliqua. Ut enim ad minim veniam, quis nostrud exercitation ullamco laboris nisi ut aliquip ex ea commodo consequat. Duis aute irure dolor in reprehenderit in voluptate velit esse cillum dolore eu fugiat nulla pariatur.</p>
      <p class="paragraph">Lorem ipsum dolor sit amet, consectetur adipiscing elit, sed do eiusmod tempor incididunt ut labore et dolore magna aliqua. Ut enim ad minim veniam, quis nostrud exercitation ullamco laboris nisi ut aliquip ex ea commodo consequat.</p>
      <p class="paragraph">Excepteur sint occaecat cupidatat non proident, sunt in culpa qui officia deserunt mollit anim id est laborum. re et dolore magnam aliquam quaerat voluptatem.</p>
      <p class="closing">Regards</p>
      <p class="signature">Daniel Reyes</p>
    </section>
  </main>
</body>
</html>
```